SirKettle needs a new packaging

We are Coffee Roasters based in Versailles France.

We want a new design for our coffee packaging. The packaging is a basic brown paper bag. We are sticking on it a 99.1mm x 67.7mm Label.

We want a new design for the label. The label should have the following info : Name of the coffee, origin, one line of description, our website www.sirkettle.fr.

Enclosed you will find our logo, as well as a picture of our current packaging

The Design should be "simple yet sophisticate".

```html
<!DOCTYPE html>
<html lang="fr">
<head>
<meta charset="utf-8">
<title>SirKettle – Coffee Label N°5</title>
<link rel="stylesheet" href="https://fonts.googleapis.com/css2?family=Open+Sans:ital,wght@0,400;0,600;0,700;1,700&display=swap">
<style>
  :root {
    --page-bg: #ffffff;
    --ink: #111008;
    --paper-light: #f0d9a4;
    --paper-mid: #c99a55;
    --paper-dark: #7a3c12;
    --paper-edge: #5a2a0b;
  }
  * { box-sizing: border-box; margin: 0; padding: 0; }
  html, body {
    width: 1200px;
    height: 1000px;
    overflow: hidden;
    background: var(--page-bg);
  }
  .canvas {
    position: relative;
    width: 1200px;
    height: 1000px;
  }
  .label {
    position: absolute;
    left: 150px;
    top: 193px;
    width: 900px;
    height: 615px;
    overflow: hidden;
    color: var(--ink);
    font-family: "Open Sans", Arial, sans-serif;
    text-align: center;
  }
  .label-paper {
    position: absolute;
    inset: 0;
    background:
      radial-gradient(ellipse 60% 55% at 48% 42%, var(--paper-light) 0%, var(--paper-mid) 55%, var(--paper-dark) 88%, var(--paper-edge) 100%);
  }
  .label-content {
    position: relative;
    height: 100%;
    padding-top: 40px;
  }
  .brand {
    display: flex;
    align-items: center;
    justify-content: center;
    gap: 26px;
  }
  .brand-dot {
    width: 118px;
    height: 118px;
    border-radius: 50%;
    background: var(--ink);
    flex: none;
  }
  .brand-text { text-align: left; }
  .brand-name {
    font-size: 72px;
    font-weight: 400;
    line-height: 1;
    letter-spacing: 1px;
    padding-bottom: 8px;
    border-bottom: 4px solid var(--ink);
  }
  .brand-tagline {
    font-size: 27px;
    font-weight: 400;
    margin-top: 8px;
    padding-left: 8px;
  }
  .coffee-name {
    font-size: 76px;
    font-weight: 400;
    line-height: 1.1;
    margin-top: 30px;
    letter-spacing: -0.5px;
  }
  .coffee-blend {
    font-size: 34px;
    line-height: 1.2;
  }
  .coffee-origin {
    font-size: 36px;
    line-height: 1.25;
  }
  .coffee-description {
    font-size: 22px;
    font-weight: 700;
    font-style: italic;
    margin-top: 14px;
  }
  .roaster-contact {
    margin-top: 44px;
    font-size: 21px;
    font-weight: 600;
    line-height: 1.3;
  }
  .roaster-contact .divider { padding: 0 8px; }
</style>
</head>
<body>
<main class="canvas">
  <section class="label">
    <div class="label-paper" role="img" aria-label="Aged parchment paper texture in warm browns with faint coffee cup ring stains"></div>
    <div class="label-content">
      <header class="brand">
        <span class="brand-dot"></span>
        <div class="brand-text">
          <div class="brand-name">SirKettle</div>
          <div class="brand-tagline">Artisan Torréfacteur</div>
        </div>
      </header>
      <h1 class="coffee-name">N°5 de SirKettle</h1>
      <p class="coffee-blend">100% Arabica</p>
      <p class="coffee-origin">(Brésil, Congo, Ethiopie)</p>
      <p class="coffee-description">Description placed here</p>
      <footer class="roaster-contact">
        <p>14 rue des Tilleuls 78000 Versailles<span class="divider">|</span>Tel. +33 1 23 45 67 89</p>
        <p>cafe-kettle-versailles.fr</p>
      </footer>
    </div>
  </section>
</main>
</body>
</html>
```